Small Business Broker Business Card Design

A business card design for a small business brokerage, which is a financial service, not unlike real estate brokerage, but for small businesses such as laundromats, pizza shops, restaurants, cleaners etc. The designs should all be simple, more conservative in nature, using the colors and font of the logo. Again, think real estate Brokerage as a business context
Contact Information for Business Card
Name: Glen R. Harlow. Title: Small Business Advisor. Email: g.harlow@bayfieldcapitalworks.example. Mobile: (555) 274-3918. Office: (555) 806-2147. www.bayfieldcapitalworks.example

```html
<!DOCTYPE html>
<html lang="en">
<head>
<meta charset="utf-8">
<title>Bayfield Capital Works – Business Card</title>
<link href="https://fonts.googleapis.com/css2?family=Montserrat:wght@400;600;700;800&display=swap" rel="stylesheet">
<style>
  :root {
    --navy: #1b3a70;
    --navy-deep: #162f5c;
    --green: #8cc63f;
    --white: #ffffff;
    --stage: #e9eaec;
  }
  * { box-sizing: border-box; margin: 0; padding: 0; }
  html, body { width: 1200px; height: 800px; overflow: hidden; }
  body {
    background: var(--stage);
    font-family: "Montserrat", Arial, sans-serif;
    display: flex; align-items: center; justify-content: center; gap: 40px;
  }
  .card {
    width: 540px; height: 309px; border-radius: 18px; overflow: hidden;
    position: relative; box-shadow: 0 6px 18px rgba(0,0,0,.18);
  }

  /* Back side */
  .card-back {
    background: var(--navy);
    display: flex; flex-direction: column; align-items: center; justify-content: center;
  }
  .back-texture {
    position: absolute; inset: 0;
    background: linear-gradient(135deg, #2a4f8f 0%, var(--navy) 45%, var(--navy-deep) 100%);
  }
  .back-brand { position: relative; text-align: center; }
  .back-brand .company {
    color: var(--white); font-weight: 800; font-size: 22px; letter-spacing: .5px;
    text-transform: uppercase;
  }
  .back-brand .tagline {
    color: var(--green); font-weight: 700; font-size: 10.5px; letter-spacing: 1.4px;
    text-transform: uppercase; margin-top: 4px;
  }

  /* Front side */
  .card-front { background: var(--white); }
  .brand-area {
    position: absolute; left: 0; right: 0; top: 0; height: 172px;
    display: flex; flex-direction: column; align-items: center; justify-content: center;
  }
  .brand-line { display: flex; align-items: center; gap: 10px; }
  .brand-mark { width: 18px; height: 18px; background: var(--green); }
  .brand-area .company {
    color: var(--navy); font-weight: 800; font-size: 27px; text-transform: uppercase;
    letter-spacing: .3px;
  }
  .brand-area .tagline {
    color: var(--green); font-weight: 700; font-size: 12px; letter-spacing: 1.6px;
    text-transform: uppercase; margin-top: 6px;
  }
  .info-band {
    position: absolute; left: 0; right: 0; bottom: 0; height: 137px;
    background: var(--navy); border-top: 2px solid var(--green);
    display: flex; align-items: center; padding: 0 28px;
  }
  .person { flex: 0 0 200px; text-align: right; padding-right: 18px; }
  .person .name { color: var(--green); font-weight: 800; font-size: 23px; }
  .person .title { color: var(--white); font-weight: 400; font-size: 12.5px; margin-top: 3px; }
  .divider { width: 1px; height: 86px; background: var(--green); }
  .contacts { list-style: none; padding-left: 16px; }
  .contacts li {
    display: flex; align-items: center; gap: 8px;
    color: var(--white); font-size: 11.5px; line-height: 20px;
  }
  .contacts svg { width: 12px; height: 12px; flex: none; fill: var(--green); }
</style>
</head>
<body>

  <section class="card card-back" aria-label="Card back">
    <div class="back-texture" role="img" aria-label="Faint repeating brand pattern on navy"></div>
    <div class="back-brand">
      <p class="company">Bayfield Capital Works, Inc</p>
      <p class="tagline">Confidently buy or sell a local business today</p>
    </div>
  </section>

  <section class="card card-front" aria-label="Card front">
    <div class="brand-area">
      <div class="brand-line">
        <span class="brand-mark"></span>
        <p class="company">Bayfield Capital Works, Inc</p>
      </div>
      <p class="tagline">Confidently buy or sell a local business today</p>
    </div>

    <div class="info-band">
      <div class="person">
        <p class="name">Glen R. Harlow</p>
        <p class="title">Small Business Advisor</p>
      </div>
      <div class="divider"></div>
      <ul class="contacts">
        <li>
          <svg viewBox="0 0 24 24" aria-hidden="true"><path d="M3 8c0-2 3-4 9-4s9 2 9 4v2h-5V8H8v2H3zM5 12h14l2 8H3z"/></svg>
          (555) 806-2147
        </li>
        <li>
          <svg viewBox="0 0 24 24" aria-hidden="true"><path d="M6.6 10.8a15 15 0 0 0 6.6 6.6l2.2-2.2c.3-.3.7-.4 1-.2 1.1.4 2.3.6 3.6.6.6 0 1 .4 1 1V20c0 .6-.4 1-1 1A17 17 0 0 1 3 4c0-.6.4-1 1-1h3.5c.6 0 1 .4 1 1 0 1.3.2 2.5.6 3.6.1.3 0 .7-.2 1z"/></svg>
          (555) 274-3918
        </li>
        <li>
          <svg viewBox="0 0 24 24" aria-hidden="true"><path d="M2 5h20v14H2zm2 2v.5l8 5 8-5V7z"/></svg>
          g.harlow@bayfieldcapitalworks.example
        </li>
        <li>
          <svg viewBox="0 0 24 24" aria-hidden="true"><path d="M12 2a10 10 0 1 0 0 20 10 10 0 0 0 0-20zm0 2c1.2 0 2.6 2.3 3 6H9c.4-3.7 1.8-6 3-6zm-3 8h6c-.4 3.7-1.8 6-3 6s-2.6-2.3-3-6z"/></svg>
          www.bayfieldcapitalworks.example
        </li>
      </ul>
    </div>
  </section>

</body>
</html>
```